Cognitive therapist.

I am a therapist and my main work is with clients who have depression and anxiety disorders.

I need something reasonably plain. Cognitive therapy is a very pragmatic approach to dealing with problems, so it isn't new agey (no offence to new age therapies at all)
Updates

Hi everyone, I am currently looking at a particular design that I will most likely go with. Cheers, Meg

Industry/Entity Type

Work

Contact Information for Business Card

Meg Tarvish
Cognitive Therapist
BA, PG Dip Mental Health,
PG Dip Cog Beh Therapy
MKTPR

The Quarry Lodge,
Level One
48 Marlow Parade
Cnr Fenwick St & Marlow Parade
P O Box 38 219
WELLINGTON 6143

Phone: 021 574 3082 Email: mtarvish@quellnet.co.nz

www.megtarvish.co.nz

Requirements
Should not have
• No illustration, or colour. not old style fonts.

```html
<!DOCTYPE html>
<html lang="en">
<head>
<meta charset="utf-8">
<title>Meg Tarvish – Business Card</title>
<link rel="stylesheet" href="https://fonts.googleapis.com/css2?family=Questrial&display=swap">
<style>
  :root {
    --page-bg: #e6e7e9;
    --card-bg: #ffffff;
    --teal: #6fcac6;
    --text-grey: #5f6163;
    --text-dark: #3d3f41;
    --rule-grey: #8a8c8e;
  }
  * { box-sizing: border-box; margin: 0; padding: 0; }
  html, body {
    width: 1200px;
    height: 1000px;
    overflow: hidden;
    background: var(--page-bg);
    font-family: "Questrial", "Century Gothic", sans-serif;
  }
  .business-card {
    position: absolute;
    left: 100px;
    top: 215px;
    width: 1000px;
    height: 571px;
    background: var(--card-bg);
    border-radius: 46px;
    box-shadow: 0 8px 28px rgba(0,0,0,0.12);
    overflow: hidden;
  }
  .identity {
    position: absolute;
    right: 530px;
    top: 150px;
    text-align: right;
    color: var(--text-grey);
  }
  .identity__name {
    font-size: 56px;
    letter-spacing: 1px;
    color: var(--teal);
    text-transform: uppercase;
    line-height: 1;
    margin-bottom: 8px;
    -webkit-text-stroke: 0.8px var(--teal);
  }
  .identity__credentials {
    font-size: 23px;
    line-height: 1.2;
  }
  .divider {
    position: absolute;
    left: 492px;
    top: 132px;
    width: 1.5px;
    height: 170px;
    background: var(--rule-grey);
  }
  .contact {
    position: absolute;
    left: 514px;
    top: 128px;
    font-size: 19px;
    line-height: 1.28;
    color: var(--text-grey);
  }
  .contact__pobox strong { color: var(--text-dark); font-weight: 700; }
  .contact__line {
    display: flex;
    align-items: center;
    gap: 6px;
  }
  .contact__icon { width: 18px; height: 18px; flex: none; }
  .contact__channels { margin-top: 6px; }
  .footer-rule {
    position: absolute;
    height: 11px;
    background: var(--teal);
    top: 452px;
  }
  .footer-rule--left { left: 0; width: 560px; }
  .footer-rule--right { left: 890px; right: 0; top: 400px; }
  .website {
    position: absolute;
    left: 580px;
    top: 424px;
    font-size: 31px;
    color: var(--text-grey);
    letter-spacing: 0.3px;
  }
</style>
</head>
<body>
  <section class="business-card">
    <div class="identity">
      <h1 class="identity__name">Meg Tarvish</h1>
      <p class="identity__credentials">Cognitive Therapist BA,<br>PG Dip Mental Health,<br>PG Dip Cog Beh Therapy MKTPR</p>
    </div>

    <div class="divider"></div>

    <address class="contact" style="font-style: normal;">
      <div>The Quarry Lodge, Level One</div>
      <div>48 Marlow Parade Cnr Fenwick St</div>
      <div>&amp; Marlow Parade</div>
      <div class="contact__pobox"><strong>P O Box</strong> 38 219 WELLINGTON 6143</div>
      <div class="contact__channels">
        <div class="contact__line">
          <svg class="contact__icon" viewBox="0 0 18 18" aria-hidden="true">
            <circle cx="9" cy="9" r="9" fill="var(--teal)"/>
            <rect x="6" y="4" width="6" height="10" rx="1.2" fill="none" stroke="#fff" stroke-width="1.3"/>
            <circle cx="9" cy="12" r="0.8" fill="#fff"/>
          </svg>
          <span>021 574 3082</span>
        </div>
        <div class="contact__line">
          <svg class="contact__icon" viewBox="0 0 18 18" aria-hidden="true">
            <circle cx="9" cy="9" r="9" fill="var(--teal)"/>
            <rect x="4.5" y="5.5" width="9" height="7" fill="none" stroke="#fff" stroke-width="1.2"/>
            <path d="M4.5 5.5 L9 9.5 L13.5 5.5" fill="none" stroke="#fff" stroke-width="1.2"/>
          </svg>
          <span>mtarvish@quellnet.co.nz</span>
        </div>
      </div>
    </address>

    <div class="footer-rule footer-rule--left"></div>
    <div class="website">www.megtarvish.co.nz</div>
    <div class="footer-rule footer-rule--right" style="top: 452px;"></div>
  </section>
</body>
</html>
```